Velorin Health is a Direct primary office that needs a great flyer design

Velorin Health has been rebranded with a new logo and website and need new flyers to fit in with our new model and direction. Please refer to velorin-example.com for content. Attached is a possible layout.

```html
<!DOCTYPE html>
<html lang="en">
<head>
<meta charset="utf-8">
<title>Velorin Health – Tri-fold Brochure</title>
<link rel="stylesheet" href="https://fonts.googleapis.com/css2?family=Lato:ital,wght@0,300;0,400;0,700;0,900;1,400&family=Montserrat:wght@800&display=swap">
<style>
:root{
  --bg:#1f1f1f;
  --blue:#3b3f9c;
  --navy:#2b3390;
  --green:#1f8a3b;
  --green-dark:#14702d;
  --white:#ffffff;
  --ink:#2a2a2a;
  --grey:#4a4a4a;
}
*{margin:0;padding:0;box-sizing:border-box}
html,body{width:770px;height:1200px;overflow:hidden;background:var(--bg)}
body{position:relative;font-family:"Lato",sans-serif;color:var(--ink)}
.sheet{position:absolute;left:35px;width:697px;height:538px;overflow:hidden}
.sheet--outside{top:45px}
.sheet--inside{top:622px}
.panel{position:absolute;top:0;height:538px;overflow:hidden}
.panel--left{left:0;width:234px;background:var(--white)}
.panel--mid{left:234px;width:225px;background:var(--blue);color:var(--white)}
.panel--right{left:459px;width:238px;background:var(--white)}
.abs{position:absolute}
.photo{position:absolute}

/* services */
.svc-kicker{top:19px;width:100%;text-align:center;font-weight:300;font-size:10px;color:var(--grey);letter-spacing:.2px}
.svc-title{top:31px;width:100%;text-align:center;font-weight:900;font-size:13px;color:var(--navy);letter-spacing:-.3px}
.svc{position:absolute;width:91px;height:91px;border-radius:50%;border:2px solid var(--green);overflow:hidden;background:var(--white)}
.svc .photo{inset:0}
.svc-label{position:absolute;left:0;right:0;bottom:0;height:24px;background:var(--navy);color:var(--white);font-size:4.6px;font-weight:900;text-align:center;line-height:5.5px;padding-top:6px;text-transform:uppercase}
.pricing-bg{left:0;top:240px;width:234px;height:298px;background:linear-gradient(160deg,#3b3f9c 0%,#3556a0 35%,#2a8f56 75%,#1f8a3b 100%)}
.pricing-title{top:320px;left:19px;font-weight:900;font-size:12.5px;color:var(--white);letter-spacing:-.3px}
.price-row{position:absolute;left:19px;color:var(--white)}
.price-row svg{position:absolute;left:0;top:0}
.price-head{position:absolute;left:35px;top:0;font-weight:900;font-size:8.5px;white-space:nowrap;letter-spacing:-.2px}
.price-text{position:absolute;left:35px;top:13px;font-size:7.6px;line-height:10px;width:180px}
.price-text.sm{font-size:7.2px}

/* why choose */
.mid-pad{left:18px;width:192px}
.why-title{top:30px;font-weight:900;font-size:13px;line-height:15.5px;letter-spacing:-.3px}
.lorem{top:67px;font-size:8px;line-height:10.1px}
.dots{height:0;border-top:2px dotted rgba(255,255,255,.9);left:18px;width:190px}
.benefit{position:absolute;left:39px;width:170px;font-size:11px;line-height:13.7px;font-weight:400}
.benefit-icon{position:absolute;left:-16px;top:1px}
.touch-title{top:355px;width:100%;text-align:center;font-weight:900;font-size:12px;letter-spacing:-.3px}
.touch-lorem{top:380px;width:100%;text-align:center;font-style:italic;font-size:8px;line-height:10.5px}
.contact{position:absolute;left:68px;font-weight:300;font-size:9px;line-height:11.5px}
.contact svg{position:absolute;left:-25px;top:2px}

/* cover */
.brand{top:27px;width:100%;text-align:center;font-family:"Lato",sans-serif;font-weight:400;font-size:17px;letter-spacing:1.5px;color:var(--navy);text-transform:uppercase}
.cover-photo{left:0;top:55px;width:238px;height:260px;background:linear-gradient(135deg,#e9ecef 0%,#c9d3dd 45%,#8aa0b4 75%,#d8dde2 100%)}
.cover-curve{left:0;top:250px}
.thumb{position:absolute;left:41px;top:241px;width:90px;height:90px;border-radius:50%;border:2px solid var(--navy);overflow:hidden;background:radial-gradient(circle at 55% 45%,#f2a25a 0%,#c4566e 35%,#d9dfe4 70%)}
.badge{position:absolute;left:112px;top:268px;width:76px;height:76px;border-radius:50%;background:var(--green);border:2px solid var(--navy);color:var(--white);text-align:center;font-family:"Montserrat",sans-serif;font-weight:800;font-size:9.5px;line-height:12.5px;padding-top:13px}
.cover-head{top:355px;width:100%;text-align:center;font-family:"Montserrat",sans-serif;font-weight:800;font-size:14.2px;line-height:18.3px}
.cover-head .b{color:var(--navy)}
.cover-head .g{color:var(--green)}
.cover-cta{left:0;top:482px}
.cta-label{top:503px;width:100%;text-align:center;color:var(--white);font-weight:300;font-size:10px;letter-spacing:.2px}
.cta-phone{top:514px;width:100%;text-align:center;color:var(--white);font-weight:900;font-size:18.5px}

/* inside left */
.sb-title{top:12px;width:100%;text-align:center;font-family:"Montserrat",sans-serif;font-weight:800;font-size:17.5px;line-height:21px;color:var(--navy)}
.sb-body{top:99px;left:14px;width:206px;text-align:center;font-size:7.6px;line-height:10px;color:var(--ink);z-index:2}
.sb-body p+p{margin-top:7px}
.sb-photo{left:0;top:262px;width:234px;height:276px;background:linear-gradient(120deg,#1d4fa0 0%,#e7e2da 40%,#d6b39c 60%,#5d7ea8 85%,#2a5fae 100%)}
.sb-swoosh{left:0;top:256px;z-index:1}

/* faq */
.faq-title{top:25px;font-weight:900;font-size:12.5px;letter-spacing:-.3px}
.faq-q{position:absolute;left:39px;width:175px;font-weight:700;font-size:11px;line-height:13.7px}
.faq-q svg{position:absolute;left:-16px;top:1px}
.faq-a{position:absolute;left:18px;width:192px;font-size:7.9px;line-height:10.1px}

/* about */
.about-photo{left:0;top:0;width:238px;height:320px;background:linear-gradient(100deg,#c9c4bf 0%,#e6e4e1 40%,#f0a24f 58%,#7a5c86 72%,#e8e8e6 100%)}
.about-title{top:306px;width:100%;text-align:center;font-family:"Montserrat",sans-serif;font-weight:800;font-size:17.5px;line-height:21px;color:var(--navy)}
.about-body{top:359px;left:16px;width:206px;text-align:center;font-size:7.8px;line-height:10.1px;color:var(--ink)}
.about-body p+p{margin-top:7px}
</style>
</head>
<body>

<section class="sheet sheet--outside">

  <div class="panel panel--left">
    <div class="abs svc-kicker">VELORIN HEALTH</div>
    <h2 class="abs svc-title">OUR SERVICES</h2>

    <div class="svc" style="left:19px;top:56px">
      <div class="photo" role="img" aria-label="Doctor examining a patient's shoulder" style="background:linear-gradient(140deg,#f2f3f5,#b9c4d2 60%,#5c7395)"></div>
      <div class="svc-label">Primary<br>Care</div>
    </div>
    <div class="svc" style="left:125px;top:56px">
      <div class="photo" role="img" aria-label="Patient on a video call with a doctor on a tablet" style="background:linear-gradient(140deg,#e9e6e1,#c7cfd8 55%,#7f97b2)"></div>
      <div class="svc-label" style="padding-top:8px">Telemedicine</div>
    </div>
    <div class="svc" style="left:19px;top:155px">
      <div class="photo" role="img" aria-label="Laboratory with monitors and equipment" style="background:linear-gradient(140deg,#1f4d78,#5e8fb8 50%,#cfe1ee)"></div>
      <div class="svc-label">Heart Function<br>Screening</div>
    </div>
    <div class="svc" style="left:125px;top:155px">
      <div class="photo" role="img" aria-label="Scan images on a diagnostic screen" style="background:linear-gradient(140deg,#0d2440,#2c5f8f 50%,#a7c3db)"></div>
      <div class="svc-label">Diagnostic<br>Ultrasound</div>
    </div>

    <div class="abs pricing-bg" role="img" aria-label="Faded photo of a senior patient under a blue to green tint"></div>
    <svg class="abs" style="left:0;top:240px" width="234" height="80" viewBox="0 0 234 80" aria-hidden="true">
      <path d="M0 0 H234 V8 Q117 72 0 14 Z" fill="#ffffff"/>
      <path d="M0 14 Q117 72 234 8 Q120 84 0 18 Z" fill="#1f8a3b"/>
    </svg>

    <h3 class="abs pricing-title">VELORIN HEALTH PRICING</h3>

    <div class="price-row" style="top:347px">
      <svg width="26" height="22" viewBox="0 0 26 22" aria-hidden="true"><circle cx="9" cy="6" r="5" fill="#fff"/><path d="M0 21 Q0 12 9 12 Q13 12 15 14 V21 Z" fill="#fff"/><rect x="15" y="12" width="10" height="9" rx="1" fill="#fff"/><path d="M17 12 V9 a3 3 0 0 1 6 0 V12" fill="none" stroke="#fff" stroke-width="1.6"/></svg>
      <div class="price-head">REGISTRATION FEE:</div>
      <div class="price-text">$50 per person. Maximum $100 for families that enroll all at the same time.</div>
    </div>

    <div class="price-row" style="top:406px">
      <svg width="20" height="20" viewBox="0 0 20 20" aria-hidden="true"><circle cx="10" cy="10" r="9.5" fill="#fff"/><circle cx="10" cy="8" r="3.3" fill="#3b58a0"/><path d="M4.5 16 Q10 10 15.5 16" fill="#3b58a0"/></svg>
      <div class="price-head" style="left:33px">INDIVIDUAL MEMBERSHIP:</div>
      <div class="price-text sm" style="left:33px;width:170px">Age 21-45: $60/month<br>Age 46-64: $80/month<br>Age 65 and over $100/month<br>Age 17-20 with parent/guardian membership: $25/month</div>
    </div>

    <div class="price-row" style="top:484px">
      <svg width="18" height="20" viewBox="0 0 18 20" aria-hidden="true"><rect x="0.5" y="3" width="17" height="16" rx="1.5" fill="#fff"/><rect x="4" y="0.5" width="2" height="4" fill="#fff"/><rect x="12" y="0.5" width="2" height="4" fill="#fff"/><g fill="#2f6aa0"><rect x="3" y="8" width="3" height="2.5"/><rect x="7.5" y="8" width="3" height="2.5"/><rect x="12" y="8" width="3" height="2.5"/><rect x="3" y="12.5" width="3" height="2.5"/><rect x="7.5" y="12.5" width="3" height="2.5"/><rect x="12" y="12.5" width="3" height="2.5"/></g></svg>
      <div class="price-head" style="left:33px">EMPLOYER MEMBERSHIP:</div>
      <div class="price-text sm" style="left:33px;width:180px">1-4 employees $65/month per employee<br>5+ employees $60/month per employee</div>
    </div>
  </div>

  <div class="panel panel--mid">
    <h2 class="abs mid-pad why-title">WHY CHOOSE<br>VELORIN HEALTH?</h2>
    <p class="abs mid-pad lorem">Lorem ipsum dolor sit amet, consectetur adipiscing elit, sed do eiusmod tempor incididunt ut labore et dolore magna aliqua. Ut enim ad minim veniam, quis nostrud exercitation ullamco laboris nisi ut aliquip</p>
    <div class="abs dots" style="top:122px"></div>

    <div class="benefit" style="top:140px"><svg class="benefit-icon" width="10" height="10" viewBox="0 0 10 10" aria-hidden="true"><circle cx="5" cy="5" r="5" fill="#fff"/><path d="M2.5 5 H7 M5 2.8 L7.2 5 L5 7.2" stroke="#3b3f9c" stroke-width="1.3" fill="none"/></svg>24/7 access to your doctor via telemedicine, text, and phone consultations</div>
    <div class="benefit" style="top:195px"><svg class="benefit-icon" width="10" height="10" viewBox="0 0 10 10" aria-hidden="true"><circle cx="5" cy="5" r="5" fill="#fff"/><path d="M2.5 5 H7 M5 2.8 L7.2 5 L5 7.2" stroke="#3b3f9c" stroke-width="1.3" fill="none"/></svg>Same day or next appointments</div>
    <div class="benefit" style="top:219px"><svg class="benefit-icon" width="10" height="10" viewBox="0 0 10 10" aria-hidden="true"><circle cx="5" cy="5" r="5" fill="#fff"/><path d="M2.5 5 H7 M5 2.8 L7.2 5 L5 7.2" stroke="#3b3f9c" stroke-width="1.3" fill="none"/></svg>Low cost labs</div>
    <div class="benefit" style="top:243px"><svg class="benefit-icon" width="10" height="10" viewBox="0 0 10 10" aria-hidden="true"><circle cx="5" cy="5" r="5" fill="#fff"/><path d="M2.5 5 H7 M5 2.8 L7.2 5 L5 7.2" stroke="#3b3f9c" stroke-width="1.3" fill="none"/></svg>Wellness Planning and health screenings</div>
    <div class="benefit" style="top:279px"><svg class="benefit-icon" width="10" height="10" viewBox="0 0 10 10" aria-hidden="true"><circle cx="5" cy="5" r="5" fill="#fff"/><path d="M2.5 5 H7 M5 2.8 L7.2 5 L5 7.2" stroke="#3b3f9c" stroke-width="1.3" fill="none"/></svg>Unlimited appointments</div>

    <div class="abs dots" style="top:314px"></div>

    <h2 class="abs touch-title">GET IN TOUCH</h2>
    <p class="abs touch-lorem">Lorem ipsum dolor sit amet, consectetur<br>adipiscing elit, sed do eiusmod tempor</p>

    <div class="contact" style="top:420px">
      <svg width="14" height="16" viewBox="0 0 14 16" aria-hidden="true"><path d="M3 1 L5.5 1 L6.5 5 L4.8 6.3 Q6.2 10 9.3 11.5 L10.7 9.8 L13.5 11 L13.5 13.5 Q12.5 15.5 10 15 Q2 12 1 3.5 Q1 1.5 3 1 Z" fill="none" stroke="#fff" stroke-width="1.3"/></svg>
      Call Us<br>555-014-2738
    </div>
    <div class="contact" style="top:453px">
      <svg width="16" height="16" viewBox="0 0 16 16" aria-hidden="true"><circle cx="8" cy="8" r="7" fill="none" stroke="#fff" stroke-width="1.4"/><path d="M3 5 Q6 4 6.5 7 Q5 9 7 11 L6.5 14 M10 2.5 Q9 5 11.5 6 Q14 6 13.5 9 Q11 9.5 11 12" fill="none" stroke="#fff" stroke-width="1.3"/></svg>
      Email Us<br>info@velorin-example.com
    </div>
    <div class="contact" style="top:488px">
      <svg width="17" height="15" viewBox="0 0 17 15" aria-hidden="true"><path d="M1 8 L8.5 1.5 L16 8" fill="none" stroke="#fff" stroke-width="1.8"/><path d="M3.5 7 V14 H7 V10 H10 V14 H13.5 V7" fill="#fff"/></svg>
      1180 Alder Creek Parkway<br>Suite C Marlow, GA 30099
    </div>
  </div>

  <div class="panel panel--right">
    <div class="abs brand">Velorin Health</div>
    <div class="photo cover-photo" role="img" aria-label="Smiling doctor with a tablet giving a high five to a young boy"></div>
    <svg class="abs cover-curve" width="238" height="110" viewBox="0 0 238 110" aria-hidden="true">
      <path d="M0 64 Q110 20 238 60 V110 H0 Z" fill="#ffffff"/>
      <path d="M0 64 Q110 14 238 60 Q110 26 0 70 Z" fill="#1f8a3b"/>
    </svg>
    <div class="thumb" role="img" aria-label="Gloved hand holding a drip bag filled with fruit"></div>
    <div class="badge">INVEST<br>IN YOUR<br>HEALTH</div>

    <h1 class="abs cover-head">
      <span class="b">VELORIN HEALTH</span><br>
      <span class="g">BENEFITS PATIENTS BY</span><br>
      <span class="b">PROVIDING SUBSTANTIAL</span><br>
      <span class="g">SAVINGS AND A GREATER</span><br>
      <span class="b">DEGREE OF ACCESS TO</span><br>
      <span class="g">YOUR DOCTOR.</span>
    </h1>

    <svg class="abs cover-cta" width="238" height="56" viewBox="0 0 238 56" aria-hidden="true">
      <path d="M0 56 V26 Q119 -18 238 26 V56 Z" fill="#1f8a3b"/>
    </svg>
    <div class="abs cta-label">CONTACT WITH US</div>
    <div class="abs cta-phone">555-014-2738</div>
  </div>
</section>

<section class="sheet sheet--inside">

  <div class="panel panel--left">
    <h2 class="abs sb-title">VELORIN HEALTH<br>A SOLUTION FOR<br>SMALL BUSINESS<br>HEALTH CARE</h2>
    <div class="abs sb-body">
      <p>At a time when many companies face the challenge of finding affordable health insurance, Direct Care shows significant savings.</p>
      <p>Healthcare affordability concerns are real. Valuable benefits such as direct primary care can help set your business apart and enable you to keep and attract quality employees. In addition, by providing Velorin Health membership, your staff is more likely to stay healthy and stay on the job thanks to the preventative care that is inherent to our in-depth doctor-patient relationship. Your workforce will benefit from text and email access to address concerns quickly as well as same or next-day appointments. These benefits will help to reduce absenteeism and</p>
    </div>
    <div class="photo sb-photo" role="img" aria-label="Nurse examining the shoulder of a smiling senior man beside anatomy posters"></div>
    <svg class="abs sb-swoosh" width="234" height="40" viewBox="0 0 234 40" aria-hidden="true">
      <path d="M0 0 Q117 40 234 0 V4 Q117 48 0 6 Z" fill="#ffffff"/>
      <path d="M0 6 Q117 48 234 4 Q117 56 0 11 Z" fill="#1f8a3b"/>
    </svg>
  </div>

  <div class="panel panel--mid">
    <h2 class="abs mid-pad faq-title">VELORIN HEALTH FAQ</h2>

    <div class="faq-q" style="top:47px"><svg width="10" height="10" viewBox="0 0 10 10" aria-hidden="true"><circle cx="5" cy="5" r="5" fill="#fff"/><path d="M2.5 5 H7 M5 2.8 L7.2 5 L5 7.2" stroke="#3b3f9c" stroke-width="1.3" fill="none"/></svg>What is direct primary care?</div>
    <p class="faq-a" style="top:68px">Direct primary care is an affordable alternative approach to health care and medical services. Instead of dealing with costly co-pays and insurance claim forms, and waiting to get reimbursed, DPC allows you to pay a monthly, quarterly, or annual fee to the health care provider of your choice. In return for this “membership” or “retainer” fee, you have access to your medical practitioner whenever you need them.</p>

    <div class="faq-q" style="top:171px"><svg width="10" height="10" viewBox="0 0 10 10" aria-hidden="true"><circle cx="5" cy="5" r="5" fill="#fff"/><path d="M2.5 5 H7 M5 2.8 L7.2 5 L5 7.2" stroke="#3b3f9c" stroke-width="1.3" fill="none"/></svg>How is a direct primary care practice different?</div>
    <p class="faq-a" style="top:208px">One of the biggest differences between DPC practices and traditional practices is that in a DPC practice, you’ll have access to your health care provider at your convenience. Visits to the office for medical exams, routine physicals, lab work, or other comprehensive health and wellness services are unlimited, so you don’t have to worry about an expensive co-pay each time you make an appointment. Your physician is there when you need them most, so you can maintain good health, get medical attention for an illness, or learn how to better manage a chronic condition.</p>

    <div class="faq-q" style="top:342px"><svg width="10" height="10" viewBox="0 0 10 10" aria-hidden="true"><circle cx="5" cy="5" r="5" fill="#fff"/><path d="M2.5 5 H7 M5 2.8 L7.2 5 L5 7.2" stroke="#3b3f9c" stroke-width="1.3" fill="none"/></svg>Will I still benefit even though I don't visit the doctor that often?</div>
    <p class="faq-a" style="top:378px">We believe that access to your doctor can be valuable, especially for questions that could be simply answered or addressed by someone who knows you, or that can prevent a visit to the emergency department or hospital. We would however encourage you to be interested in “well-ness” and would want to become your partner in an overall wellness and in prevention care plan for you. Access to care includes emails and phone visits which are included in the monthly fee and should be considered a valuable service. Because you will not be burdened with co-pays with our accessible schedules, the process of coming in for an appoint-ment will be easy and not rushed.</p>
  </div>

  <div class="panel panel--right">
    <div class="photo about-photo" role="img" aria-label="Gloved hand holding up a drip bag filled with orange, kiwi, plum and grapes"></div>
    <svg class="abs" style="left:0;top:268px" width="238" height="60" viewBox="0 0 238 60" aria-hidden="true">
      <path d="M0 42 Q120 -10 238 38 V60 H0 Z" fill="#ffffff"/>
      <path d="M0 42 Q120 -16 238 38 Q120 2 0 46 Z" fill="#1f8a3b"/>
    </svg>
    <h2 class="abs about-title">ABOUT<br>OUR PRACTICE</h2>
    <div class="abs about-body">
      <p>Our mission is to provide patient-centered care that is respectful, honest and compassionate.</p>
      <p>Our goal is to make a significant impact on the lives of people in the surrounding communities through health education, better care and disease prevention.</p>
      <p>We believe that health care should revolve around decisions that patients make between themselves and their doctor, not what the insurance-controlled model dictates because of cost, time or convenience. As a Direct Primary Care provider, we focus on you and your health without the interference of outside interests. Our model allows more time with you, 24/7 access to your provider, which we believe is critical to developing relationships and making appropriate decisions for wellness, medical care and chronic care management.</p>
    </div>
  </div>
</section>

</body>
</html>
```